Vegan bakery needs business card

We need a business card design for my vegan bakery in Philadelphia Pa. We create amazing whole food plant based cuisine that is egg and dairy free. We use fruits, vegetables, healing herbs, nuts, natural sugars (date, turbinado, agave) and non bleached flours in our creations. Due to demand and interest in the Philadelphia area we created a late night vegan dessert delivery service named Bramble Vegan. We are the only business providing delicious vegan desserts delivered to your door at 1am!! We would like to see designs that use the color scheme in the logo. The final design should communicate the benefits of our products: dairy/egg free, plant based, healing herbs, amazing food.

```html
<!DOCTYPE html>
<html lang="en">
<head>
<meta charset="UTF-8">
<title>Bramble Vegan – Business Card</title>
<link href="https://fonts.googleapis.com/css2?family=Quicksand:wght@500;700&family=Open+Sans:wght@600&family=Arimo:wght@400;700&display=swap" rel="stylesheet">
<style>
  :root {
    --coral: #ee7b67;
    --leaf: #5cb83a;
    --ink: #3d3d3d;
    --paper: #ffffff;
    --backdrop: #e9e9ea;
  }
  html, body {
    margin: 0;
    width: 1200px;
    height: 675px;
    overflow: hidden;
    background: var(--backdrop);
  }
  .stage {
    position: relative;
    width: 1200px;
    height: 675px;
    display: flex;
    align-items: center;
    justify-content: center;
    gap: 40px;
  }
  .card {
    position: relative;
    width: 525px;
    height: 300px;
    background: var(--paper);
    box-shadow: 0 6px 18px rgba(0,0,0,0.12);
    overflow: hidden;
  }
  .brand {
    display: flex;
    flex-direction: column;
    align-items: center;
    font-family: 'Quicksand', sans-serif;
  }
  .brand__name {
    display: flex;
    align-items: center;
    gap: 8px;
    color: var(--coral);
    font-weight: 700;
    font-size: 34px;
    line-height: 1;
  }
  .brand__dot {
    width: 14px;
    height: 14px;
    border-radius: 50%;
    background: var(--leaf);
  }
  .brand__tagline {
    margin-top: 12px;
    color: var(--leaf);
    font-weight: 500;
    font-size: 21px;
    line-height: 1.05;
    text-align: center;
  }
  /* Front */
  .card--front .brand {
    position: absolute;
    top: 58px;
    left: 0;
    right: 0;
  }
  .benefits-band {
    position: absolute;
    left: 0;
    right: 0;
    bottom: 40px;
    height: 32px;
    background: var(--coral);
    color: var(--paper);
    font-family: 'Open Sans', sans-serif;
    font-weight: 600;
    font-size: 15px;
    display: flex;
    align-items: center;
    justify-content: center;
    letter-spacing: 0.2px;
  }
  /* Back */
  .card--back {
    display: flex;
    align-items: center;
  }
  .card--back .brand {
    width: 235px;
    flex: none;
  }
  .card--back .brand__name { font-size: 28px; }
  .card--back .brand__tagline { font-size: 18px; }
  .divider {
    width: 2px;
    height: 150px;
    background: var(--coral);
    flex: none;
  }
  .contact {
    padding-left: 24px;
    font-family: 'Arimo', sans-serif;
    color: var(--ink);
    font-size: 14px;
    line-height: 1.2;
  }
  .contact__name { font-weight: 700; font-size: 15px; }
  .contact__title { margin-bottom: 12px; }
  .contact__address { margin-bottom: 10px; }
  .contact__row {
    display: flex;
    align-items: center;
    gap: 8px;
  }
  .contact__row svg { width: 13px; height: 13px; flex: none; }
</style>
</head>
<body>
<main class="stage">
  <section class="card card--front" aria-label="Business card front">
    <div class="brand">
      <div class="brand__name"><span class="brand__dot"></span>Bramble Vegan</div>
      <div class="brand__tagline">100% vegan<br>100% delicious</div>
    </div>
    <div class="benefits-band">Dairy/egg free, Plant based, Healing Herbs, Amazing Food</div>
  </section>

  <section class="card card--back" aria-label="Business card back">
    <div class="brand">
      <div class="brand__name"><span class="brand__dot"></span>Bramble Vegan</div>
      <div class="brand__tagline">100% vegan<br>100% delicious</div>
    </div>
    <div class="divider"></div>
    <div class="contact">
      <div class="contact__name">Employee Name</div>
      <div class="contact__title">Title</div>
      <div class="contact__address">Bay Area HQ<br>2140 Larkmoor Street- Suite 310<br>Oakland, CA 94602</div>
      <div class="contact__row">
        <svg viewBox="0 0 16 16" aria-hidden="true"><circle cx="8" cy="8" r="8" fill="#ee7b67"/><path d="M5.5 4.5l1.6 0 .6 2-1 .8a5 5 0 0 0 2 2l.8-1 2 .6v1.6c-3.5.3-6.3-2.5-6-6z" fill="#fff"/></svg>
        <span>(510) 555- 0147</span>
      </div>
      <div class="contact__row">
        <svg viewBox="0 0 16 16" aria-hidden="true"><rect x="1" y="3" width="14" height="10" rx="1.5" fill="#ee7b67"/><path d="M2 4.5l6 4.5 6-4.5" stroke="#fff" stroke-width="1.3" fill="none"/></svg>
        <span>info@website.com</span>
      </div>
      <div class="contact__row">
        <svg viewBox="0 0 16 16" aria-hidden="true"><g fill="none" stroke="#ee7b67" stroke-width="1.3"><circle cx="8" cy="8" r="6.5"/><ellipse cx="8" cy="8" rx="3" ry="6.5"/><path d="M1.5 8h13M2.5 4.8h11M2.5 11.2h11"/></g></svg>
        <span>www.website.com</span>
      </div>
    </div>
  </section>
</main>
</body>
</html>
```